I need a business card for my original fine art pieces

I would like a business card design including a logo design for a new business in the art world. I am based in the Hunter Valley NSW Australia. I am a contemporary figurative, encaustic and wildlife artist. I would like to be able to upload my email and mobile number to this as well. This design should be one that I can incorporate into banners and flyers etc. Id like to incorporate one of my own images or partial image into the background or somewhere below. My initials are RJ and I would like these used as a logo type. I would like the use of some colour and it to be bright and catchy. The final design should communicate artwork custom made and commissions available.

Overview: Original Fine Artworks for sale, online, art galleries etc, Custom made to order and by commission.

Target market is world wide audience and corporate world

My figurative work is painted using acrylics in a lot of natural ochre colours that reflect the Australian Outback, on canvas, linen, paper or board: My encaustic work is created in a contemporary abstract style using a blow torch and a made with a medium of 100% pure bees wax, Damar resin, mixed media and coloured pigments, applied to Birch board. My wildlife are created using coloured pencil and mixed media on a variety of paper types or board.

```html
<!DOCTYPE html>
<html lang="en">
<head>
<meta charset="utf-8">
<title>Rhea Jansen – Business Card</title>
<link href="https://fonts.googleapis.com/css2?family=Cinzel:wght@400;600&family=Open+Sans:wght@400;600&display=swap" rel="stylesheet">
<style>
  :root {
    --stage: #e4e3e1;
    --card-dark: #262626;
    --card-dark-edge: #1b1b1b;
    --card-light: #f7f7f6;
    --accent: #ee5a24;
    --ink: #333333;
    --ink-soft: #7a7a7a;
    --on-dark: #f2f2f2;
    --rule: #c9c9c9;
  }
  * { box-sizing: border-box; margin: 0; padding: 0; }
  html, body { width: 1200px; height: 1000px; overflow: hidden; }
  body {
    background: var(--stage);
    font-family: "Open Sans", Arial, sans-serif;
    display: flex;
    flex-direction: column;
    align-items: center;
    justify-content: center;
    gap: 70px;
  }
  .card {
    width: 630px;
    height: 360px;
    position: relative;
    overflow: hidden;
    box-shadow: 0 10px 30px rgba(0,0,0,.18);
  }

  /* shared brand block */
  .brand { display: flex; align-items: center; gap: 22px; }
  .brand-dot {
    width: 104px; height: 104px;
    border: 3px solid var(--accent);
    border-radius: 50%;
    flex: none;
  }
  .brand-name {
    font-family: "Cinzel", Georgia, serif;
    font-weight: 600;
    font-size: 40px;
    line-height: 1;
    color: var(--accent);
    letter-spacing: 1px;
    white-space: nowrap;
  }
  .brand-tagline {
    font-size: 17px;
    letter-spacing: 3.4px;
    color: var(--on-dark);
    margin-top: 6px;
    text-transform: uppercase;
    white-space: nowrap;
  }

  /* front */
  .card-front { background: var(--card-light); }
  .front-band {
    position: absolute; left: 0; top: 0;
    width: 100%; height: 168px;
    background: linear-gradient(180deg, #2c2c2c, var(--card-dark-edge));
    padding: 32px 40px;
  }
  .front-body {
    position: absolute; left: 0; top: 168px;
    width: 100%; height: 192px;
    display: flex; align-items: center;
    padding: 0 40px;
  }
  .holder { width: 250px; }
  .holder-name {
    font-size: 30px; font-weight: 600; color: var(--ink); line-height: 1.1;
    white-space: nowrap;
  }
  .holder-name .surname { color: var(--accent); }
  .holder-role { font-size: 16px; color: var(--ink); margin-top: 4px; padding-left: 70px; }
  .divider { width: 1px; height: 120px; background: var(--rule); margin: 0 26px; }
  .contact { font-size: 15px; color: var(--ink-soft); line-height: 1.55; }
  .contact li { list-style: none; display: flex; align-items: center; gap: 9px; white-space: nowrap; }
  .contact .icon { width: 12px; height: 12px; flex: none; fill: var(--accent); }
  .contact .hl { color: var(--accent); }

  /* back */
  .card-back {
    background: radial-gradient(ellipse at 55% 40%, #3a3a3a, #202020 75%);
    display: flex; align-items: center; justify-content: center;
  }
  .card-back .brand { flex-direction: row-reverse; gap: 26px; }
  .card-back .brand-dot { width: 128px; height: 128px; }
  .back-text { text-align: left; }
  .back-web {
    display: flex; align-items: center; gap: 9px;
    font-size: 15px; color: var(--on-dark); margin-top: 18px; letter-spacing: .5px;
  }
  .back-web .hl { color: var(--accent); }
  .back-web .icon { width: 13px; height: 13px; fill: var(--accent); }
</style>
</head>
<body>

  <section class="card card-front" aria-label="Business card front">
    <div class="front-band">
      <div class="brand">
        <div class="brand-dot" aria-hidden="true"></div>
        <div>
          <div class="brand-name">RHEA JANSEN</div>
          <div class="brand-tagline">Original Fine Artworks</div>
        </div>
      </div>
    </div>
    <div class="front-body">
      <div class="holder">
        <div class="holder-name">Daniel <span class="surname">Brooks</span></div>
        <div class="holder-role">Director</div>
      </div>
      <div class="divider"></div>
      <ul class="contact">
        <li>Your Street Address</li>
        <li>Pokolbin, 2320</li>
        <li>
          <svg class="icon" viewBox="0 0 12 12" aria-hidden="true"><path d="M2.5 0.5 L4.5 0.5 L5.3 3.2 L4 4.3 C4.7 5.9 6 7.3 7.7 8 L8.8 6.7 L11.5 7.5 L11.5 9.5 C11.5 10.6 10.6 11.5 9.5 11.5 C4.5 11.2 0.8 7.5 0.5 2.5 C0.5 1.4 1.4 0.5 2.5 0.5 Z"/></svg>
          +000 11223 4455
        </li>
        <li>
          <svg class="icon" viewBox="0 0 12 12" aria-hidden="true"><path d="M0 2 H12 V10 H0 Z M0.8 2.6 L6 6.6 L11.2 2.6 L11.2 3.6 L6 7.6 L0.8 3.6 Z" fill-rule="evenodd"/></svg>
          hello@rheajansen.art
        </li>
        <li>
          <svg class="icon" viewBox="0 0 12 12" aria-hidden="true"><circle cx="6" cy="6" r="6"/></svg>
          <span>www.<span class="hl">rheajansenart</span>.com</span>
        </li>
      </ul>
    </div>
  </section>

  <section class="card card-back" aria-label="Business card back">
    <div class="brand">
      <div class="brand-dot" aria-hidden="true"></div>
      <div class="back-text">
        <div class="brand-name">RHEA JANSEN</div>
        <div class="brand-tagline">Original Fine Artworks</div>
        <div class="back-web">
          <svg class="icon" viewBox="0 0 12 12" aria-hidden="true"><circle cx="6" cy="6" r="6"/></svg>
          <span>www.<span class="hl">rheajansenart</span>.com</span>
        </div>
      </div>
    </div>
  </section>

</body>
</html>
```